Velmora Freightway Solutions Business cards

Would like a very unique design catchy but professional for business cards. Please use log provided.Marlon WellsCeo and Founder TransCon Logistix Solutions1-888-913-3225mwells@tlsolutionsus.comwww.tlsolutionsus.com

```html
<!DOCTYPE html>
<html lang="en">
<head>
<meta charset="utf-8">
<title>Velmora Freightway Solutions – Business Cards</title>
<link href="https://fonts.googleapis.com/css2?family=Open+Sans:wght@400;600;700&display=swap" rel="stylesheet">
<style>
  :root{
    --stage:#1c1c1e;
    --brand-blue:#0f72ba;
    --brand-red:#e5202a;
    --paper:#ffffff;
    --ink-white:#ffffff;
  }
  *{margin:0;padding:0;box-sizing:border-box}
  html,body{width:1200px;height:960px;overflow:hidden}
  body{
    background:var(--stage);
    font-family:"Open Sans",Arial,sans-serif;
    position:relative;
  }
  .card{
    position:absolute;
    left:250px;
    width:700px;
    height:400px;
    overflow:hidden;
  }
  /* Back side */
  .card-back{
    top:50px;
    background:var(--brand-blue);
    display:flex;
    flex-direction:column;
    align-items:center;
    justify-content:center;
    gap:26px;
    color:var(--ink-white);
  }
  .back-brand{
    display:flex;
    align-items:center;
    gap:18px;
    font-size:40px;
    font-weight:700;
    letter-spacing:1px;
  }
  .brand-square{
    width:34px;height:34px;
    background:var(--ink-white);
  }
  .back-url{
    font-size:20px;
    font-weight:600;
    letter-spacing:3px;
  }
  /* Front side */
  .card-front{
    top:490px;
    background:var(--paper);
  }
  .front-shapes{position:absolute;inset:0}
  .front-brand{
    position:absolute;
    left:40px;
    top:120px;
    width:300px;
    color:var(--brand-blue);
    font-weight:700;
    font-size:25px;
    line-height:1.2;
    display:flex;
    align-items:center;
    gap:14px;
  }
  .front-brand .brand-square{background:var(--brand-red);width:26px;height:26px;flex:none}
  .brand-rule{
    position:absolute;
    left:40px;
    top:210px;
    width:280px;
    height:2px;
    background:var(--brand-red);
  }
  .contact{
    position:absolute;
    right:40px;
    top:70px;
    text-align:right;
    color:var(--ink-white);
    font-size:17px;
    line-height:1.45;
  }
  .contact-name{font-size:23px;font-weight:700;letter-spacing:.5px}
  .contact-title{font-size:18px;margin-bottom:14px}
  .contact-address{margin-bottom:14px}
  .contact-line{display:flex;justify-content:flex-end;align-items:center;gap:10px}
  .contact-line svg{width:16px;height:16px;flex:none}
</style>
</head>
<body>

  <section class="card card-back">
    <div class="back-brand"><span class="brand-square"></span>Velmora Freightway</div>
    <div class="back-url">www.vfwayroutes.com</div>
  </section>

  <section class="card card-front">
    <svg class="front-shapes" viewBox="0 0 700 400" width="700" height="400">
      <circle cx="690" cy="330" r="330" fill="var(--brand-red)"/>
      <circle cx="702" cy="330" r="326" fill="var(--brand-blue)"/>
    </svg>

    <div class="front-brand"><span class="brand-square"></span>Velmora Freightway Solutions</div>
    <div class="brand-rule"></div>

    <div class="contact">
      <div class="contact-name">DORIAN PIKE</div>
      <div class="contact-title">CEO AND FOUNDER</div>
      <div class="contact-address">2417 Harlow Mill Rd<br>Atlanta, GA 30318</div>
      <div class="contact-line">1-888-470-6158
        <svg viewBox="0 0 16 16"><circle cx="8" cy="8" r="7.5" fill="#fff"/><path d="M5 4.5l1.6-.4 1 2.2-1 .8a5 5 0 0 0 2.3 2.3l.8-1 2.2 1-.4 1.6c-3.5.3-6.8-3-6.5-6.5z" fill="var(--brand-blue)"/></svg>
      </div>
      <div class="contact-line">dpike@vfwayroutes.com
        <svg viewBox="0 0 16 16"><circle cx="8" cy="8" r="7.5" fill="#fff"/><rect x="4" y="5" width="8" height="6" fill="none" stroke="var(--brand-blue)" stroke-width="1.2"/><path d="M4 5l4 3.5L12 5" fill="none" stroke="var(--brand-blue)" stroke-width="1.2"/></svg>
      </div>
      <div class="contact-line">www.vfwayroutes.com
        <svg viewBox="0 0 16 16"><circle cx="8" cy="8" r="7.5" fill="#fff"/><circle cx="8" cy="8" r="4.5" fill="none" stroke="var(--brand-blue)" stroke-width="1.1"/><path d="M3.5 8h9M8 3.5c-2 2.5-2 6.5 0 9M8 3.5c2 2.5 2 6.5 0 9" fill="none" stroke="var(--brand-blue)" stroke-width="1.1"/></svg>
      </div>
    </div>
  </section>

</body>
</html>
```